International business needs business cards

Our company, DRV Ventures Inc. is in the business of supplying a range construction products with particular emphasis on CEMENT. We have developed our own brand - TORVAN SUPPLIES - with which to infiltrate the market. We are launching our brand of cement (TORVAN Type IS Cement) into the Caribbean which is unlike anything this market has ever seen. A monopoly has existed here for the past 60-odd years and the market has now opened to allow the importation of other brands and consumers are anxious and ready for change/improvement. We are very excited to be launching and want to make a great first impression. We will be conducting workshops and seminars (from government level to the hardware store owners) and we want our business card to give us the strong, confident introduction that we need.

Target Market(s)

construction; builders; engineers; home owners

Industry/Entity Type

Construction

Contact Information for Business Card

Marisol Depree
CEO
cell # 1 555 4180736
Ground floor,Lindell Plaza Suite 2734
George Town,Grand Cayman
Cayman Islands,KY1-4823
EMAIL: m.depree@drvventuresinc.example
web site drvventuresinc.example

COMPANY: skype info drv.ventures.example

second card
Yvette Brannock-Depree
CFO
CELL# 1 555 607 3941
George Town,Grand Cayman
Cayman Islands,KY1-4823
EMAIL: y.brannockdepree@drvventuresinc.example
website drvventuresinc.example

Requirements
Must have
• Business cards must display BOTH logos - DRV is the company and TORVAN is the brand.

```html
<!DOCTYPE html>
<html lang="en">
<head>
<meta charset="utf-8">
<title>DRV Ventures Inc. – Business Cards</title>
<link rel="stylesheet" href="https://fonts.googleapis.com/css2?family=Source+Sans+3:wght@400;600;700;800&display=swap">
<style>
  :root {
    --backdrop: #e6e3de;
    --card-black: #121212;
    --card-white: #ffffff;
    --brand-red: #8a1a1c;
    --ink: #1a1a1a;
    --ink-soft: #333333;
    --badge-grey: #6d6d6d;
    --shadow: rgba(0,0,0,0.22);
  }
  * { box-sizing: border-box; margin: 0; padding: 0; }
  html, body {
    width: 1200px; height: 900px; overflow: hidden;
    background: var(--backdrop);
    font-family: "Source Sans 3", "Helvetica Neue", Arial, sans-serif;
  }
  .sheet {
    position: relative; width: 1200px; height: 900px;
    display: flex; flex-direction: column; align-items: center; justify-content: center; gap: 50px;
  }
  .card {
    position: relative; width: 630px; height: 360px; overflow: hidden;
    box-shadow: 0 6px 18px var(--shadow);
  }

  /* Front */
  .card--front {
    background:
      repeating-linear-gradient(0deg, rgba(255,255,255,0.035) 0 1px, transparent 1px 4px),
      var(--card-black);
    display: flex; align-items: center; justify-content: center;
  }
  .wordmark { display: flex; align-items: center; gap: 14px; }
  .wordmark__square { width: 96px; height: 96px; background: var(--brand-red); flex: none; }
  .wordmark__name { font-weight: 800; line-height: 0.95; color: #ffffff; }
  .wordmark__name .big { display: block; font-size: 74px; letter-spacing: 2px; }
  .wordmark__name .small { display: block; font-size: 19px; letter-spacing: 1px; text-transform: uppercase; }

  /* Back */
  .card--back { background: var(--card-white); color: var(--ink); }
  .card__bands { position: absolute; inset: 0; }
  .contact-name {
    position: absolute; left: 88px; top: 24px; font-size: 21px; font-weight: 700; color: var(--ink);
  }
  .contact-name .surname { color: var(--brand-red); }
  .contact-role { position: absolute; left: 88px; top: 52px; font-size: 13px; color: var(--ink-soft); }
  .address {
    position: absolute; left: 60px; top: 118px; font-size: 15px; line-height: 19px; color: var(--ink-soft);
    font-style: normal;
  }
  .contact-list {
    position: absolute; left: 46px; top: 186px; list-style: none; font-size: 15px; line-height: 21px; color: var(--ink-soft);
  }
  .contact-list li { display: flex; align-items: center; gap: 10px; }
  .contact-list svg { width: 11px; height: 11px; fill: var(--brand-red); flex: none; }
  .card--back .wordmark { position: absolute; left: 338px; top: 100px; gap: 10px; }
  .card--back .wordmark__square { width: 82px; height: 82px; }
  .card--back .wordmark__name { color: var(--ink); }
  .card--back .wordmark__name .big { font-size: 62px; }
  .card--back .wordmark__name .small { font-size: 16px; }
  .brand-mark {
    position: absolute; left: 380px; top: 212px; display: flex; align-items: center; gap: 10px;
  }
  .brand-mark__circle { width: 62px; height: 62px; border-radius: 50%; background: var(--badge-grey); }
  .brand-mark__name { font-size: 18px; font-weight: 700; color: var(--ink); letter-spacing: 1px; }
</style>
</head>
<body>
<main class="sheet">
  <section class="card card--front" aria-label="Card front">
    <div class="wordmark">
      <span class="wordmark__square"></span>
      <span class="wordmark__name"><span class="big">DRV</span><span class="small">Ventures Inc.</span></span>
    </div>
  </section>

  <section class="card card--back" aria-label="Card back">
    <svg class="card__bands" viewBox="0 0 630 360" width="630" height="360" aria-hidden="true">
      <polygon points="22,18 52,18 30,60 22,60" fill="#121212"/>
      <polygon points="52,18 76,18 54,60 30,60" fill="#8a1a1c"/>
      <polygon points="0,282 250,282 232,302 0,302" fill="#121212"/>
      <polygon points="232,302 630,302 630,360 196,360" fill="#8a1a1c"/>
      <polygon points="250,282 630,282 630,302 232,302" fill="#ffffff"/>
    </svg>

    <h1 class="contact-name">Marisol <span class="surname">Depree</span></h1>
    <p class="contact-role">CEO</p>

    <address class="address">
      Ground floor, Lindell Plaza Suite 2734<br>
      George Town, Grand Cayman<br>
      Cayman Islands, KY1-4823
    </address>

    <ul class="contact-list">
      <li><svg viewBox="0 0 12 12"><rect x="3" y="0" width="6" height="12" rx="1"/></svg>1 555 4180736</li>
      <li><svg viewBox="0 0 12 12"><rect x="0" y="2" width="12" height="8"/></svg>m.depree@drvventuresinc.example</li>
      <li><svg viewBox="0 0 12 12"><circle cx="6" cy="6" r="6"/></svg>www.drvventuresinc.example</li>
    </ul>

    <div class="wordmark">
      <span class="wordmark__square"></span>
      <span class="wordmark__name"><span class="big">DRV</span><span class="small">Ventures Inc.</span></span>
    </div>

    <div class="brand-mark">
      <span class="brand-mark__circle"></span>
      <span class="brand-mark__name">TORVAN SUPPLIES</span>
    </div>
  </section>
</main>
</body>
</html>
```